Web Design Project

Psychotherapy and Counselling Practice needs a landing page web design.

My business "Larkfield Advisory" specialises in the treatment of Anxiety and Depression with a holistic approach, endeavouring to unlock the key that holds us to ransom in a life that is imbalanced, frustrating, and ultimately of our own making due to our own perceptions and behaviours.

There is much that impacts us which we cannot change, but we are always in control of how we think, and how we frame our experiences.....learning to challenge those thoughts and behaviours that are destructive and disempowering opens up a world of joyful possibility. Life is about making choices, learn to make wiser and healthier choices.......

Larkfield Advisory has a client base of individual clients but will seek to expand to offer services to the Corporate world by offering an adjunct to employers for established "Wellness Programs".

Larkfield Advisory is a highly professional, ethically bound business, with the needs of the client at the forefront of all we do.

Larkfield Advisory wishes to avoid the usual "jargon driven" psychobabble offered on many counselling web pages. It aims to be stylishly presented, clean in look and with as few "words" as possible and a largely white background (faster loading and more powerful impact of what is stated), those words contained in the webpage should be meaningful, persuasive and have an impact simply at glance. Larkfield does not want , or expect, those prospective clients in need of support , to be reading through volumes of industry driven cliches.

At this point Larkfield is just looking for a high quality landing page. However in time this will likely expand to include other sections such as case studies, video content etc.

Target Market(s)

Those in need of emotional support, suffering mental health issues, and those simply wanting to become self aware supported by a mindful therapist.

Industry/Entity Type

Industry

Requirements
Must have
• The design must incorporate the Larkfield logo and colour schemes found on the attached files.

```html
<!DOCTYPE html>
<html lang="en">
<head>
<meta charset="utf-8">
<title>Larkfield Advisory — Landing Page</title>
<link rel="stylesheet" href="https://fonts.googleapis.com/css2?family=Open+Sans:wght@300;400;600&display=swap">
<style>
  :root {
    --green: #8cb51b;
    --green-dark: #7a9f12;
    --grey-panel: #777777;
    --grey-dark: #5f5f5f;
    --text-dark: #4a4a4a;
    --text-body: #555555;
    --white: #ffffff;
    --line: #dcdcdc;
  }
  * { box-sizing: border-box; margin: 0; padding: 0; }
  html, body { width: 1200px; height: 1200px; overflow: hidden; }
  body {
    position: relative;
    background: var(--white);
    font-family: "Open Sans", Arial, sans-serif;
    color: var(--text-body);
  }
  a { text-decoration: none; }
  .abs { position: absolute; }

  /* bands */
  .band-top { left: 0; top: 0; width: 1200px; height: 280px; background: var(--green); }
  .band-grey { left: 0; top: 280px; width: 1200px; height: 283px;
    background: linear-gradient(180deg, #858585 0%, #7a7a7a 60%, #6f6f6f 100%); }
  .strip-top { left: 171px; top: 0; width: 365px; height: 20px; background: #dfe8c4; }

  /* contact */
  .phone-box { left: 837px; top: 0; width: 192px; height: 30px; background: var(--white);
    font-size: 21px; color: var(--text-dark); display: flex; align-items: center; padding-left: 8px; gap: 10px; }
  .phone-box .tag { font-weight: 600; color: var(--green-dark); }
  .account-links { left: 914px; top: 44px; font-size: 11px; font-weight: 600; color: #2d3a08; }
  .account-links span { margin: 0 5px; color: #55700c; }

  /* logo panel */
  .logo-panel { left: 171px; top: 36px; width: 365px; height: 326px; }
  .logo-name { left: 196px; top: 180px; font-size: 49px; font-weight: 300; color: var(--white); letter-spacing: 1px; }
  .social { display: flex; gap: 6px; }
  .social i { display: block; width: 25px; height: 25px; border-radius: 50%; background: var(--white); }
  .social-head { left: 403px; top: 54px; }

  /* navigation */
  .main-nav { left: 536px; top: 69px; width: 493px; height: 46px; background: var(--green-dark);
    display: flex; align-items: center; padding-left: 21px; }
  .main-nav a, .foot-nav a { color: var(--white); font-weight: 600; font-size: 19px; }
  .foot-nav a { font-size: 18px; }
  .main-nav .sep, .foot-nav .sep { width: 1px; height: 12px; background: rgba(255,255,255,.6); margin: 0 10px; }

  /* hero copy */
  .hero-title { left: 557px; top: 127px; font-size: 38px; font-weight: 300; color: var(--white); white-space: nowrap; }
  .hero-sub { left: 557px; top: 180px; width: 480px; font-size: 24px; font-weight: 300; line-height: 30px; color: var(--text-dark); }
  .intro { left: 196px; top: 371px; font-size: 24px; font-weight: 300; line-height: 33px; color: var(--white); white-space: nowrap; }

  .search { left: 336px; top: 519px; width: 200px; height: 22px; border-radius: 11px; background: #f2f2f2;
    border: 1px solid #cfcfcf; font-size: 11px; color: #555; padding: 3px 0 0 9px; }
  .search svg { position: absolute; right: 8px; top: 4px; }

  /* media */
  .portrait { left: 560px; top: 240px; width: 470px; height: 384px;
    background: radial-gradient(ellipse at 55% 55%, #f4f4f4 0%, #dcdcdc 45%, rgba(130,130,130,0) 75%); }
  .video { left: 171px; top: 553px; width: 365px; height: 247px;
    background: radial-gradient(ellipse at 40% 35%, #6a6a6a 0%, #2a2a2a 50%, #0d0d0d 100%);
    border: 8px solid #1b1b1b; }
  .video svg { position: absolute; left: 160px; top: 100px; }

  /* statement */
  .statement { left: 557px; top: 632px; font-size: 24px; font-weight: 300; line-height: 32px; color: var(--text-dark); white-space: nowrap; }
  .statement em { font-style: normal; font-weight: 400; color: var(--green-dark); }

  .btn { display: block; background: var(--green); color: var(--white); font-weight: 600; font-size: 14px;
    text-align: center; line-height: 32px; height: 32px; letter-spacing: .3px; }
  .btn-consult { left: 556px; top: 767px; width: 144px; }

  /* columns */
  .col { top: 856px; }
  .col h2 { font-size: 25px; font-weight: 400; color: var(--green-dark); line-height: 30px; white-space: nowrap; }
  .col p { margin-top: 16px; font-size: 12.5px; line-height: 20px; color: var(--text-body); }
  .col .btn { position: absolute; top: 150px; width: 147px; }
  .col-1 { left: 196px; width: 228px; }
  .col-2 { left: 459px; width: 236px; }
  .col-3 { left: 727px; width: 268px; }
  .divider { top: 860px; width: 1px; height: 180px; background: var(--line); }
  .divider::before { content: ""; position: absolute; left: -2px; top: 0; width: 4px; height: 26px; background: var(--green); }

  /* footer */
  .footer { left: 0; top: 1077px; width: 1200px; height: 123px; background: var(--green); }
  .foot-nav { left: 196px; top: 1105px; display: flex; align-items: center; }
  .copyright { left: 196px; top: 1149px; font-size: 12px; color: #2f3f05; }
  .social-foot { left: 716px; top: 1102px; }
  .foot-logo { left: 861px; top: 1061px; width: 146px; height: 126px; }
  .foot-logo-name { left: 872px; top: 1116px; font-size: 21px; font-weight: 300; color: var(--white); }
</style>
</head>
<body>
  <div class="abs band-top"></div>
  <div class="abs band-grey"></div>
  <div class="abs strip-top"></div>

  <svg class="abs" style="left:536px;top:540px" width="500" height="90" viewBox="0 0 500 90">
    <path d="M0 23 C150 95 350 70 495 23 L495 0 L0 0 Z" fill="#777"/>
    <path d="M0 23 C150 95 350 70 495 23 C350 80 160 100 0 40 Z" fill="#8cb51b"/>
  </svg>

  <div class="abs phone-box"><span class="tag">M</span>0400 118 207</div>
  <div class="abs account-links">Login<span>|</span>Register</div>

  <svg class="abs logo-panel" viewBox="0 0 365 326" role="presentation">
    <path d="M0 0 H365 V290 C250 262 110 270 0 300 Z" fill="#777777"/>
    <path d="M0 300 C110 270 250 262 365 290 V302 C250 276 110 282 0 326 Z" fill="#5f5f5f"/>
  </svg>
  <div class="abs social social-head"><i></i><i></i><i></i><i></i></div>
  <div class="abs logo-name">LARKFIELD</div>

  <nav class="abs main-nav">
    <a href="#">HOME</a><span class="sep"></span>
    <a href="#">ABOUT</a><span class="sep"></span>
    <a href="#">SERVICES</a><span class="sep"></span>
    <a href="#">CONTACT</a><span class="sep"></span>
    <a href="#">FAQS</a>
  </nav>

  <h1 class="abs hero-title">Your wellness starts today</h1>
  <p class="abs hero-sub">specialises in the treatment of Anxiety and Depression with a holistic approach</p>

  <p class="abs intro">Dr. MARA ELLISON commitment<br>to provide quality healthcare<br>for your whole family drives<br>everything we do.</p>

  <div class="abs search">Search
    <svg width="13" height="13" viewBox="0 0 13 13"><circle cx="5" cy="5" r="4" fill="none" stroke="#555" stroke-width="1.6"/><path d="M8 8 L12 12" stroke="#555" stroke-width="1.8"/></svg>
  </div>

  <div class="abs portrait" role="img" aria-label="Smiling doctor in a white coat gesturing towards the headline"></div>

  <div class="abs video" role="img" aria-label="Video still of a person sitting alone with head in hands">
    <svg width="34" height="34" viewBox="0 0 34 34"><path d="M4 2 L32 17 L4 32 Z" fill="#ffffff" fill-opacity=".85"/></svg>
  </div>

  <p class="abs statement"><em>Larkfield Advisory is a highly<br>professional, ethically bound business,</em><br>with the needs of the client at the forefront<br>of all we do.</p>
  <a class="abs btn btn-consult" href="#">CONSULT US</a>

  <div class="abs divider" style="left:437px"></div>
  <div class="abs divider" style="left:711px"></div>

  <section class="abs col col-1">
    <h2>Who We Are</h2>
    <p>Lorem ipsum dolor sit amet, consectetuer adipiscing elit, sed diam nonummy nibh euismod tincidunt ut laoreet dolore magna aliquam erat volutpat.</p>
    <a class="btn" href="#">GET TO KNOW US</a>
  </section>
  <section class="abs col col-2">
    <h2>We’re Growing!</h2>
    <p>Ut wisi enim ad minim veniam, quis nostrud exerci tation ullamcorper suscipit lobortis nisl ut aliquip ex ea commodo consequat.</p>
    <a class="btn" href="#">HOW WE HELPS</a>
  </section>
  <section class="abs col col-3">
    <h2>Let’s Talk about You</h2>
    <p>Duis autem vel eum iriure dolor in hendrerit in vulputate velit esse molestie consequat, vel illum dolore eu feugiat nulla facilisis at vero eros et accumsan et iusto odio.</p>
    <a class="btn" href="#">CONSULT US</a>
  </section>

  <footer class="abs footer"></footer>
  <nav class="abs foot-nav">
    <a href="#">HOME</a><span class="sep"></span>
    <a href="#">ABOUT</a><span class="sep"></span>
    <a href="#">SERVICES</a><span class="sep"></span>
    <a href="#">CONTACT</a><span class="sep"></span>
    <a href="#">FAQS</a>
  </nav>
  <div class="abs copyright">Copyright © 2013 Larkfield</div>
  <div class="abs social social-foot"><i></i><i></i><i></i><i></i></div>

  <svg class="abs foot-logo" viewBox="0 0 146 126" role="presentation">
    <path d="M0 0 H146 V112 C100 100 45 104 0 118 Z" fill="#777777"/>
    <path d="M0 118 C45 104 100 100 146 112 V118 C100 108 45 112 0 126 Z" fill="#5f5f5f"/>
  </svg>
  <div class="abs foot-logo-name">LARKFIELD</div>
</body>
</html>
```